Business Card Re-Design/Update

We'd like to update out business cards. I've included our current "Style guide" which has the colour scheme of the organisation in it. I've also included the branding files with logos etc in them.

I've also included a copy of one of our existing cards so that you can see how ugly/dated they look. I'd like a fresh modern corporate look.

Target Market(s)

These are for our clients, potential clients, industry contacts - like all business cards

Contact Information for Business Card

Name
Position
Company Address - Level 1, 47 Fernby Street, Carlow Qld 4072
Direct Phone
mobile
Email
Website -www.korvalit.com.au
Logo

Colors

Designer to choose colors to be used in the design.

Requirements
Must have
• Main Logo
• Cards will need to be editable to be able to personalize them for each new employee.
Nice to have
• The MapOut, ShipWell, KeepSteady would be okay to have if they can be sensibly and professionally added to the look without detracting from the main imagery.
• Maybe they could go on the back of the card? will leave this to your creative discretion as to whether/where they fit.
Should not have
• Should not have decorative or script fonts

```html
<!DOCTYPE html>
<html lang="en">
<head>
<meta charset="utf-8">
<title>korvalIT business card – front and back</title>
<link rel="stylesheet" href="https://fonts.googleapis.com/css2?family=Poppins:wght@400;500&family=Arimo:wght@400&display=swap">
<style>
  :root {
    --stage: #2b2b2d;
    --card: #1e1f21;
    --card-edge: #26272a;
    --brand-red: #e3171d;
    --wordmark: #d9d9d9;
    --body-text: #b9b9bb;
    --rule: #4a4b4e;
    --ship-blue: #2f9ae0;
    --keep-magenta: #c8239c;
    --map-green: #5fae3c;
  }
  * { box-sizing: border-box; margin: 0; padding: 0; }
  html, body { width: 1200px; height: 1108px; overflow: hidden; background: var(--stage); }
  .stage { position: relative; width: 1200px; height: 1108px; }
  .card {
    position: absolute; top: 194px; width: 440px; height: 720px;
    background: var(--card); border-radius: 24px;
    box-shadow: 0 18px 40px rgba(0,0,0,.45);
  }
  .card--front { left: 120px; text-align: center; }
  .card--back { left: 640px; overflow: hidden; }

  .mark { display: block; margin: 0 auto; background: var(--brand-red); }
  .card--front .mark { width: 56px; height: 56px; margin-top: 92px; }

  .wordmark {
    font-family: "Poppins", sans-serif; font-weight: 500;
    color: var(--wordmark); letter-spacing: -1px; line-height: 1;
  }
  .card--front .wordmark { font-size: 66px; margin-top: 18px; }

  .person-name {
    font-family: "Poppins", sans-serif; font-weight: 500;
    color: var(--brand-red); font-size: 24px; margin-top: 52px;
    text-transform: uppercase; letter-spacing: .5px;
  }
  .person-role {
    font-family: "Arimo", sans-serif; color: var(--body-text);
    font-size: 19px; margin-top: 4px;
  }
  .rule { height: 1px; background: var(--rule); margin: 20px auto 0; width: 250px; }
  .contact-icons { display: flex; justify-content: center; gap: 4px; margin-top: 18px; }
  .contact-icons svg { width: 24px; height: 24px; display: block; }
  .contact-list, .address {
    font-family: "Arimo", sans-serif; color: var(--body-text);
    font-size: 19px; line-height: 25px; list-style: none;
  }
  .contact-list { margin-top: 10px; }
  .address { margin-top: 20px; font-style: normal; }

  .pattern-field {
    position: absolute; inset: 0 0 300px 0;
    background: linear-gradient(160deg, #27282b 0%, #222326 60%, var(--card) 100%);
  }
  .back-lockup {
    position: absolute; top: 440px; left: 40px; right: 40px;
    display: flex; align-items: center; gap: 16px;
  }
  .back-lockup .mark { width: 44px; height: 44px; margin: 0; }
  .back-lockup .wordmark { font-size: 54px; }
  .card--back .rule { position: absolute; top: 520px; left: 40px; width: 360px; margin: 0; }

  .service {
    position: absolute; display: flex; align-items: center; gap: 10px;
    font-family: "Poppins", sans-serif; font-weight: 400; font-size: 32px; line-height: 1;
  }
  .service i { display: block; width: 22px; height: 22px; }
  .service--ship { top: 548px; left: 40px; color: var(--ship-blue); }
  .service--ship i { background: var(--ship-blue); }
  .service--keep { top: 606px; left: 120px; color: var(--keep-magenta); }
  .service--keep i { background: var(--keep-magenta); }
  .service--map { top: 664px; left: 220px; color: var(--map-green); }
  .service--map i { background: var(--map-green); }
</style>
</head>
<body>
<main class="stage">

  <section class="card card--front" aria-label="Card front">
    <span class="mark" aria-hidden="true"></span>
    <h1 class="wordmark">korvalIT</h1>
    <p class="person-name">Mara Delling</p>
    <p class="person-role">Business Development Manager</p>
    <div class="rule"></div>
    <div class="contact-icons" aria-hidden="true">
      <svg viewBox="0 0 24 24"><rect width="24" height="24" fill="#e3171d"/><path d="M8 6l3 3-1.5 1.5a7 7 0 0 0 4 4L15 13l3 3-2 2C11 18 6 13 6 8z" fill="#1e1f21"/></svg>
      <svg viewBox="0 0 24 24"><rect width="24" height="24" fill="#e3171d"/><rect x="8" y="5" width="8" height="14" rx="1.5" fill="#1e1f21"/></svg>
      <svg viewBox="0 0 24 24"><rect width="24" height="24" fill="#e3171d"/><rect x="6" y="10" width="12" height="8" fill="#1e1f21"/><rect x="8" y="5" width="8" height="5" fill="#1e1f21"/></svg>
      <svg viewBox="0 0 24 24"><rect width="24" height="24" fill="#e3171d"/><rect x="5" y="7" width="14" height="10" fill="#1e1f21"/><path d="M5 7l7 6 7-6" stroke="#e3171d" stroke-width="1.5" fill="none"/></svg>
      <svg viewBox="0 0 24 24"><rect width="24" height="24" fill="#e3171d"/><circle cx="12" cy="12" r="6.5" fill="#1e1f21"/><path d="M5.5 12h13M12 5.5v13" stroke="#e3171d" stroke-width="1.2"/></svg>
    </div>
    <ul class="contact-list">
      <li>+61 (0)412 560 318</li>
      <li>+61 (0)7 3184 6200</li>
      <li>+61 (0)7 3184 6209</li>
      <li>mdelling@korvalit.com.au</li>
      <li>www.korvalit.com.au</li>
    </ul>
    <div class="rule"></div>
    <address class="address">Level 1, 47 Fernby Street<br>Carlow Qld 4072</address>
  </section>

  <section class="card card--back" aria-label="Card back">
    <div class="pattern-field" role="img" aria-label="Faint tonal brand pattern across the upper card"></div>
    <div class="back-lockup">
      <span class="mark" aria-hidden="true"></span>
      <span class="wordmark">korvalIT</span>
    </div>
    <div class="rule"></div>
    <p class="service service--ship"><i aria-hidden="true"></i>ShipWell</p>
    <p class="service service--keep"><i aria-hidden="true"></i>KeepSteady</p>
    <p class="service service--map"><i aria-hidden="true"></i>MapOut</p>
  </section>

</main>
</body>
</html>
```